Marrowby Water Taxi and Transport Business Card

I need business cards for my new water taxi and freight transport business I have started here in Kodiak Alaska. Kodiak is a remote island in the middle of the gulf of Alaska. There are seven native villages around the island and Kodiak is the #2 fishing port in the United States. We also have the largest Coast Guard Base in the U.S. My company will be providing water taxi and freight transport logistics to the villages and many hunting and fishing lodges as well as remote properties around the island.

I would like a business card that isn't status quo, something that stands out, either in feel or appearance. I do like clean minimal designs but it needs to have the necessary contact info on it.

Target Market(s)

remote lodge / property owners, residents of the many villages around Kodiak and any one wanting to enjoy the great outdoors of Kodiak Alaska

Industry/Entity Type

Business

Contact Information for Business Card

I like clean simple designs that aren't cluttered but still provide the necessary information

Colors
0255a3
3277b5
33a4d5
9bcb3c
add136
fbed22
ffc214
f78f20
f37122

Requirements
Must have
• logo and contact info
• Captain Mason Elwick
• www.marrowbyferryline.com
• mason@marrowbyferryline.com

```html
<!DOCTYPE html>
<html lang="en">
<head>
<meta charset="utf-8">
<title>Marrowby Water Taxi and Transport – Business Card</title>
<link rel="stylesheet" href="https://fonts.googleapis.com/css2?family=Open+Sans:wght@400;600;700&display=swap">
<style>
  :root {
    --navy: #0255a3;
    --mid-blue: #3277b5;
    --sky: #33a4d5;
    --orange: #f78f20;
    --sun: #ffc214;
    --white: #ffffff;
    --paper: #f4f4f2;
    --steel: #9aa3ab;
  }
  * { margin: 0; padding: 0; box-sizing: border-box; }
  html, body {
    width: 1200px; height: 913px; overflow: hidden;
    background: var(--paper);
    font-family: "Open Sans", Arial, sans-serif;
  }
  .canvas { position: relative; width: 1200px; height: 913px; }

  .card {
    position: absolute; width: 540px; height: 308px; overflow: hidden;
    box-shadow: 0 6px 18px rgba(0,0,0,0.18);
  }

  /* Front */
  .card-front {
    left: 70px; top: 130px;
    background: linear-gradient(160deg, var(--sky) 0%, var(--mid-blue) 35%, var(--navy) 100%);
    color: var(--white);
  }
  .card-front .bands { position: absolute; inset: 0; }
  .logo-art {
    position: absolute; left: 34px; top: 32px; width: 170px; height: 96px;
    border-radius: 6px;
    background: linear-gradient(180deg, rgba(255,194,20,0.55) 0%, rgba(51,164,213,0.6) 45%, rgba(154,163,171,0.8) 100%);
  }
  .brand-name {
    position: absolute; left: 34px; top: 138px; width: 220px;
    font-weight: 600; font-size: 17px; line-height: 1.25; color: var(--white);
  }
  .captain {
    position: absolute; right: 34px; top: 102px;
    font-weight: 700; font-size: 19px; letter-spacing: 0.2px;
  }
  .contacts {
    position: absolute; left: 34px; top: 218px; list-style: none;
    font-size: 13px; line-height: 1.6;
  }
  .contacts li { display: flex; align-items: center; gap: 8px; }
  .contacts svg { width: 13px; height: 13px; flex: none; }

  /* Back */
  .card-back {
    left: 600px; top: 470px;
    background: var(--white);
  }
  .card-back .bands { position: absolute; inset: 0; }
  .mark-art {
    position: absolute; left: 170px; top: 40px; width: 220px; height: 190px;
    border-radius: 10px;
    background: linear-gradient(180deg, rgba(255,194,20,0.55) 0%, rgba(51,164,213,0.55) 45%, rgba(154,163,171,0.75) 100%);
  }
</style>
</head>
<body>
<main class="canvas">

  <section class="card card-front" aria-label="Business card front">
    <svg class="bands" viewBox="0 0 540 308" preserveAspectRatio="none" aria-hidden="true">
      <line x1="250" y1="128" x2="540" y2="70" stroke="var(--sky)" stroke-width="1.2"/>
      <line x1="20" y1="200" x2="520" y2="200" stroke="var(--sky)" stroke-width="1" opacity="0.7"/>
      <polygon points="0,278 300,278 320,292 540,292 540,308 0,308" fill="var(--orange)"/>
      <polygon points="300,262 540,262 540,292 320,292" fill="var(--sky)"/>
    </svg>
    <div class="logo-art" role="img" aria-label="Logo artwork: ferry boat before snowy mountains and an orange sun"></div>
    <p class="brand-name">Marrowby Water Taxi and Transport</p>
    <h1 class="captain">Captain Mason Elwick</h1>
    <ul class="contacts">
      <li>
        <svg viewBox="0 0 16 16" aria-hidden="true"><rect x="1" y="3" width="14" height="10" rx="1" fill="none" stroke="var(--orange)" stroke-width="1.6"/><polyline points="1,4 8,9 15,4" fill="none" stroke="var(--orange)" stroke-width="1.6"/></svg>
        mason@marrowbyferryline.com
      </li>
      <li>
        <svg viewBox="0 0 16 16" aria-hidden="true"><circle cx="8" cy="8" r="6.5" fill="none" stroke="var(--orange)" stroke-width="1.5"/><ellipse cx="8" cy="8" rx="3" ry="6.5" fill="none" stroke="var(--orange)" stroke-width="1.2"/><line x1="1.5" y1="8" x2="14.5" y2="8" stroke="var(--orange)" stroke-width="1.2"/></svg>
        www.marrowbyferryline.com
      </li>
    </ul>
  </section>

  <section class="card card-back" aria-label="Business card back">
    <svg class="bands" viewBox="0 0 540 308" preserveAspectRatio="none" aria-hidden="true">
      <polygon points="0,286 540,250 540,308 0,308" fill="var(--mid-blue)"/>
      <polygon points="440,0 540,0 540,250 440,257" fill="var(--navy)"/>
    </svg>
    <div class="mark-art" role="img" aria-label="Large logo artwork: ferry boat on waves before mountains and an orange sun"></div>
  </section>

</main>
</body>
</html>
```